Business card design needed

I would like a one sided black business card with the information provided above. Refer to my website www.brightvolleyracquets.com.au for an example of colors I have used for my site, would like to keep this consistent for my business cards also, I will upload my logo below.

I am a new small business that provides tennis customers with racquet re stringing, tennis strings and accessories.

Industry/Entity Type

Small Business

Contact Information for Business Card

Bright Volley Tennis

Owen Whitby
Managing Director

brightvolleyracquets@mailbox.example
www.brightvolleyracquets.com.au
0491 726 305

Racquet Restringing/Tennis Strings/Accessories

Requirements
Must have
• Must have my logo and card must be black

```html
<!DOCTYPE html>
<html lang="en">
<head>
<meta charset="utf-8">
<title>Bright Volley Tennis – Business Card</title>
<link href="https://fonts.googleapis.com/css2?family=Exo+2:wght@300;400;700&display=swap" rel="stylesheet">
<style>
  :root {
    --card-black: #030303;
    --lime: #b5d334;
    --navy-blue: #2b4f86;
    --white: #ffffff;
    --divider-grey: #9a9a9a;
    --backdrop: #7a4f33;
  }
  * { box-sizing: border-box; margin: 0; padding: 0; }
  html, body {
    width: 1200px;
    height: 475px;
    overflow: hidden;
  }
  body {
    background: var(--backdrop);
    font-family: "Exo 2", Arial, sans-serif;
    position: relative;
  }
  .card {
    position: absolute;
    top: 80px;
    width: 547px;
    height: 313px;
    background: var(--card-black);
    overflow: hidden;
  }
  .card--front { left: 34px; }
  .card--back { left: 602px; }

  .brand {
    position: absolute;
    left: 0;
    right: 0;
    display: flex;
    align-items: center;
    justify-content: center;
    gap: 10px;
    color: var(--lime);
    font-weight: 700;
    text-transform: uppercase;
    letter-spacing: 1px;
    white-space: nowrap;
  }
  .brand__dot {
    display: block;
    border-radius: 50%;
    background: var(--lime);
    flex: none;
  }
  .card--front .brand { top: 72px; font-size: 24px; }
  .card--front .brand__dot { width: 30px; height: 30px; }
  .card--back .brand { top: 118px; font-size: 27px; }
  .card--back .brand__dot { width: 36px; height: 36px; }

  .person {
    position: absolute;
    left: 62px;
    top: 172px;
    color: var(--lime);
  }
  .person__name {
    font-size: 20px;
    font-weight: 400;
    letter-spacing: 0.5px;
    text-transform: uppercase;
    line-height: 1.1;
  }
  .person__role {
    font-size: 14px;
    font-weight: 300;
    margin-top: 3px;
  }
  .divider {
    position: absolute;
    left: 226px;
    top: 168px;
    width: 2px;
    height: 58px;
    background: linear-gradient(to bottom, transparent, var(--divider-grey) 30%, var(--white) 50%, var(--divider-grey) 70%, transparent);
  }
  .contact {
    position: absolute;
    left: 240px;
    top: 175px;
    list-style: none;
    color: var(--white);
    font-size: 13.5px;
    font-weight: 400;
    line-height: 21px;
    white-space: nowrap;
  }
  .contact__item { display: flex; align-items: center; gap: 6px; }
  .contact__icon { width: 11px; height: 11px; fill: var(--white); flex: none; }

  .swoosh {
    position: absolute;
    left: 0;
    bottom: 0;
    width: 547px;
    height: 313px;
  }
  .website {
    position: absolute;
    left: 0;
    right: 0;
    text-align: center;
    color: var(--white);
    font-weight: 400;
  }
  .card--front .website {
    top: 264px;
    font-size: 14px;
    letter-spacing: 0.6px;
  }
  .card--back .website {
    top: 252px;
    font-size: 14px;
    letter-spacing: 2.4px;
  }
</style>
</head>
<body>

  <section class="card card--front" aria-label="Business card front">
    <div class="brand">
      <span class="brand__dot"></span>
      <span class="brand__name">Bright Volley Tennis</span>
    </div>

    <div class="person">
      <p class="person__name">Owen Whitby</p>
      <p class="person__role">Managing Director</p>
    </div>

    <div class="divider"></div>

    <ul class="contact">
      <li class="contact__item">
        <svg class="contact__icon" viewBox="0 0 12 12" aria-hidden="true">
          <path d="M2.5 0.8 L4.4 3.2 L3.4 4.6 C4.1 6.1 5.9 7.9 7.4 8.6 L8.8 7.6 L11.2 9.5 L10 11.2 C5.2 11 1 6.8 0.8 2 Z"/>
        </svg>
        <span>0491 726 305</span>
      </li>
      <li class="contact__item">
        <svg class="contact__icon" viewBox="0 0 12 12" aria-hidden="true">
          <path d="M0.5 2.5 H11.5 V10 H0.5 Z M1.2 3.2 L6 7 L10.8 3.2" fill="none" stroke="#ffffff" stroke-width="1.3"/>
        </svg>
        <span>brightvolleyracquets@mailbox.example</span>
      </li>
    </ul>

    <svg class="swoosh" viewBox="0 0 547 313" aria-hidden="true">
      <path d="M0 248 Q270 222 547 276 L547 283 Q270 234 0 257 Z" fill="var(--lime)"/>
      <path d="M0 261 Q270 238 547 289 L547 313 L0 313 Z" fill="var(--navy-blue)"/>
    </svg>

    <p class="website">www.brightvolleyracquets.com.au</p>
  </section>

  <section class="card card--back" aria-label="Business card back">
    <div class="brand">
      <span class="brand__dot"></span>
      <span class="brand__name">Bright Volley Tennis</span>
    </div>
    <p class="website">www.brightvolleyracquets.com.au</p>
  </section>

</body>
</html>
```